Spring Detox sale graphics for social media

You MUST read the Brief in the WORD document and follow the instructions there. I want to create 10 social media graphics (new Instagram size 4:5 (1080 x 1350 pixels) focusing on our Mother’s Day Spring Detox Sale graphics, using any of the pics attached. Use the attached pics, NO RANDOM STOCK PHOTOGRAPHY. For the color scheme of the graphics, they should all be complementary to the product colors or feel like Spring time.

Target Market(s)

primarily women

Requirements
Must have
• the photos and text attached

```html
<!DOCTYPE html>
<html lang="en">
<head>
<meta charset="utf-8">
<title>Mother's Day Spring Detox Sale</title>
<link rel="stylesheet" href="https://fonts.googleapis.com/css2?family=Figtree:wght@700;800&display=swap">
<style>
  :root {
    --page: #ffffff;
    --teal: #85bab9;
    --teal-deep: #71afae;
    --pink: #cf5c7e;
    --pink-light: #f6dde6;
    --photo-light: #f1eeed;
    --photo-warm: #d8c3b8;
    --white: #ffffff;
  }
  * { margin: 0; padding: 0; box-sizing: border-box; }
  html, body {
    width: 1200px; height: 1200px; overflow: hidden;
    background: var(--page);
  }
  .sale-post {
    position: absolute; left: 159px; top: 143px;
    width: 884px; height: 884px;
    background: var(--teal);
    overflow: hidden;
    font-family: "Figtree", sans-serif;
    color: var(--white);
  }
  .backdrop { position: absolute; left: 0; top: 0; }
  .title-banner { position: absolute; left: 0; top: 0; }
  .title-text {
    position: absolute; left: 160px; top: 8px; width: 563px;
    text-align: center; font-weight: 700; font-size: 57px;
    line-height: 58px; letter-spacing: 0.5px;
  }
  .offer {
    position: absolute; left: 0; top: 150px; width: 884px;
    text-align: center; font-weight: 700; font-size: 86px;
    line-height: 100px; letter-spacing: -0.5px;
  }
  .model-photo {
    position: absolute; left: 254px; top: 285px; width: 376px; height: 540px;
    border-radius: 150px 150px 8px 8px;
    background: radial-gradient(ellipse at 50% 40%, var(--photo-light) 0%, var(--photo-warm) 100%);
  }
</style>
</head>
<body>
  <main class="sale-post">
    <svg class="backdrop" width="884" height="884" viewBox="0 0 884 884" role="img" aria-label="Soft teal backdrop with spring leaves and pale flowers">
      <defs>
        <radialGradient id="floorGlow" cx="50%" cy="30%" r="65%">
          <stop offset="0%" stop-color="var(--pink-light)"/>
          <stop offset="100%" stop-color="var(--pink)"/>
        </radialGradient>
      </defs>
      <path d="M61 330 C100 280 160 265 230 272 C320 282 380 350 450 350 C550 350 620 320 710 330 C800 345 828 460 828 560 L828 884 L61 884 L61 560 C61 470 45 400 61 330 Z" fill="var(--teal-deep)"/>
      <polygon points="159,783 724,783 866,884 18,884" fill="url(#floorGlow)"/>
    </svg>

    <svg class="title-banner" width="884" height="134" viewBox="0 0 884 134" aria-hidden="true">
      <polygon points="191,0 692,0 723,134 160,134" fill="var(--pink)"/>
    </svg>
    <h1 class="title-text">Mother's Day<br>Spring Detox Sale</h1>

    <p class="offer">25% Off Everything!</p>

    <div class="model-photo" role="img" aria-label="Smiling woman in a white cropped sweater standing behind a row of hormone and detox supplement bottles and creams"></div>
  </main>
</body>
</html>
```